FunBrixo Business Card

We need a business card design for our company. We sell construction-themed amusement rides for kids.

Contact Information for Business Card

Contact info on business card should include:
Carl Dunning
Co-Founder & COO
(833) 571-FUNBRIX
Carl@funbrixo-demo.com
www.funbrixo-demo.com

```html
<!DOCTYPE html>
<html lang="en">
<head>
<meta charset="utf-8">
<title>FunBrixo Business Card</title>
<link rel="stylesheet" href="https://fonts.googleapis.com/css2?family=Arimo:wght@400;700&display=swap">
<style>
  :root {
    --backdrop: #4a3f3a;
    --card: #141414;
    --orange: #f0642a;
    --text-light: #d8d8d8;
    --silver: #c9c9c9;
    --divider: #6a6a6a;
  }
  * { margin: 0; padding: 0; box-sizing: border-box; }
  html, body { width: 1200px; height: 844px; overflow: hidden; }
  body {
    background: var(--backdrop);
    font-family: "Arimo", Arial, sans-serif;
    position: relative;
  }
  .card {
    position: absolute;
    top: 267px;
    width: 540px;
    height: 310px;
    background: var(--card);
    border-radius: 3px;
  }
  .card-front { left: 40px; }
  .card-back { left: 620px; }

  .brand-name {
    position: absolute;
    left: 0; right: 0;
    text-align: center;
    font-weight: 700;
    line-height: 1;
  }
  .card-front .brand-name {
    top: 62px;
    font-size: 50px;
    color: var(--orange);
  }
  .card-back .brand-name {
    top: 125px;
    font-size: 60px;
    color: var(--silver);
  }

  .person {
    position: absolute;
    right: 310px;
    top: 204px;
    text-align: right;
  }
  .person-name {
    font-size: 21px;
    font-weight: 700;
    color: var(--orange);
    letter-spacing: 0.5px;
  }
  .person-title {
    margin-top: 4px;
    font-size: 16px;
    color: var(--text-light);
  }
  .divider {
    position: absolute;
    left: 246px;
    top: 180px;
    width: 1px;
    height: 70px;
    background: var(--divider);
  }
  .contact-list {
    position: absolute;
    left: 262px;
    top: 178px;
    list-style: none;
  }
  .contact-item {
    display: flex;
    align-items: center;
    gap: 8px;
    height: 25px;
    font-size: 15px;
    color: var(--text-light);
  }
  .contact-icon { width: 15px; height: 15px; flex: none; }
</style>
</head>
<body>
  <section class="card card-front" aria-label="Business card front">
    <div class="brand-name">FunBrixo</div>

    <div class="person">
      <div class="person-name">CARL DUNNING</div>
      <div class="person-title">Co-Founder &amp; COO</div>
    </div>

    <div class="divider"></div>

    <ul class="contact-list">
      <li class="contact-item">
        <svg class="contact-icon" viewBox="0 0 16 16" aria-hidden="true">
          <rect x="0.75" y="0.75" width="14.5" height="14.5" rx="2" fill="none" stroke="#f0642a" stroke-width="1.5"/>
          <path d="M5 4.5 6.5 4 7.5 6.5 6.5 7.3c.5 1.2 1.2 1.9 2.2 2.3l.8-1 2.5 1-.5 1.5C8 11.5 4.5 8 5 4.5Z" fill="#f0642a"/>
        </svg>
        (833) 571-FUNBRIX
      </li>
      <li class="contact-item">
        <svg class="contact-icon" viewBox="0 0 16 16" aria-hidden="true">
          <rect x="0" y="3" width="16" height="10" rx="1" fill="#f0642a"/>
          <path d="M0.5 3.5 8 9l7.5-5.5" fill="none" stroke="#141414" stroke-width="1.3"/>
        </svg>
        Carl@funbrixo-demo.com
      </li>
      <li class="contact-item">
        <svg class="contact-icon" viewBox="0 0 16 16" aria-hidden="true">
          <circle cx="8" cy="8" r="7.5" fill="#f0642a"/>
          <g fill="none" stroke="#141414" stroke-width="1">
            <ellipse cx="8" cy="8" rx="3" ry="7.5"/>
            <path d="M0.5 8h15M2 4.5h12M2 11.5h12"/>
          </g>
        </svg>
        www.funbrixo-demo.com
      </li>
    </ul>
  </section>

  <section class="card card-back" aria-label="Business card back">
    <div class="brand-name">FunBrixo</div>
  </section>
</body>
</html>
```